food delivery web site design

Currently we have a smartphone app (ios/android) that is being used by our clients to make orders to about 30 different restaurants.

We would like to extent this and have also a website that is able to mimic the same functionalities:
- register
- show restaurants based on the selected address
- make order to an restaurant
- being able to process orders for other registered users (please read the attached doc for complete info on this)

Take a look at the attached doc for more info.

```html
<!DOCTYPE html>
<html lang="ro">
<head>
<meta charset="utf-8">
<title>PlateGo – La Hanul Vechi – Meniu</title>
<link href="https://fonts.googleapis.com/css2?family=Oswald:wght@300;400&family=Open+Sans:ital,wght@0,400;0,600;1,600&display=swap" rel="stylesheet">
<style>
:root{
  --red:#a11b0d;
  --red-line:#c8402e;
  --brown:#2b2120;
  --yellow:#f4c94a;
  --ink:#222;
  --muted:#666;
  --grey:#9a9a9a;
  --rule:#d9d9d9;
  --menu-ghost:#d0d0d0;
  --green:#3f9a1f;
  --footer:#1d1d1d;
  --pattern:#f2f2f2;
}
*{box-sizing:border-box;margin:0;padding:0}
html,body{width:1200px;height:923px;overflow:hidden;background:#fff}
.page{position:relative;width:1300px;height:1000px;transform:scale(0.923077);transform-origin:0 0;font-family:"Open Sans",sans-serif;color:var(--ink)}
.cond{font-family:"Oswald",sans-serif;text-transform:uppercase}

.pattern-band{position:absolute;left:0;top:0;width:1300px;height:55px;background:var(--pattern)}
.top-bar{position:absolute;left:0;top:55px;width:1300px;height:58px;background:var(--red);border-top:2px solid var(--red-line);border-bottom:2px solid var(--red-line)}
.top-bar .rule{position:absolute;top:27px;height:1px;background:rgba(255,255,255,.6)}
.top-bar .dots{position:absolute;left:660px;top:26px;width:300px;border-top:2px dotted rgba(255,255,255,.5)}
.call{position:absolute;left:379px;top:10px;color:#fff;font-size:26px;display:flex;align-items:center;gap:8px;letter-spacing:-.3px}
.call .phone{color:var(--yellow);display:flex;align-items:center;gap:4px}
.auth{position:absolute;top:16px;color:#fff;font-size:16px;display:flex;align-items:center;gap:6px}

.brand-badge{position:absolute;left:150px;top:0;width:170px;height:172px}
.brand-circle{position:absolute;left:176px;top:24px;width:120px;height:120px;border-radius:50%;background:#fff;display:flex;align-items:center;justify-content:center;font-family:"Open Sans",sans-serif;font-weight:600;font-size:22px;color:var(--red)}

.cart{position:absolute;left:960px;top:113px;width:190px;height:135px;background:var(--brown);color:#fff;z-index:3}
.cart-head{height:35px;display:flex;border-bottom:1px solid #4a3d3b}
.cart-title{flex:1;display:flex;align-items:center;gap:7px;padding-left:10px;font-size:15px}
.cart-detail{width:64px;background:var(--yellow);color:var(--brown);font-size:14px;display:flex;align-items:center;justify-content:center}
.cart-item{height:30px;display:flex;align-items:center;justify-content:space-between;padding:0 10px 0 13px;font-size:12px}
.cart-item .pm{font-size:18px;font-weight:600;font-family:"Open Sans",sans-serif;letter-spacing:6px}

.menu-ghost{position:absolute;left:975px;top:222px;font-size:84px;color:var(--menu-ghost);font-weight:400;line-height:1}

.resto-logo{position:absolute;left:150px;top:248px;width:68px;height:54px;background:linear-gradient(135deg,#6b5240,#3d2c22)}
.resto-name{position:absolute;left:229px;top:242px;font-size:32px;color:var(--red);line-height:1.1}
.rating{position:absolute;left:230px;top:290px;display:flex;align-items:center;gap:5px}
.rating a{margin-left:8px;font-size:11px;font-weight:600;color:var(--green);text-decoration:underline}
.meta{position:absolute;top:255px;display:flex;align-items:center;gap:6px;font-size:20px;color:#333}

.tabs{position:absolute;left:150px;top:321px;width:1000px;height:40px;border-top:1px solid var(--rule);border-bottom:1px solid var(--rule);display:flex;justify-content:space-between;align-items:center;font-size:20px;color:var(--grey);font-weight:300}
.tabs .active{color:var(--red)}

.menu-grid{position:absolute;left:150px;top:398px;width:1000px;height:469px;border-bottom:1px solid var(--rule);display:grid;grid-template-columns:330px 320px 350px}
.col{border-right:1px solid var(--rule)}
.col:last-child{border-right:0}
.col:nth-child(2){padding-left:20px}
.col:nth-child(3){padding-left:20px}
.dish{height:78px;display:flex;justify-content:space-between;align-items:flex-start;padding-top:3px;border-bottom:2px dotted var(--rule);margin-right:0}
.col:first-child .dish{margin-right:0;padding-right:11px}
.col:nth-child(2) .dish{padding-right:13px}
.col:nth-child(3) .dish{padding-right:34px}
.dish:last-child{border-bottom:0}
.dish-name{font-size:19px;line-height:26px}
.dish-price{font-size:19px;color:var(--muted);line-height:26px}
.dish-price em{font-size:15px;font-weight:600;color:#555}
.qty{margin-top:17px;width:70px;height:32px;border:1px solid #ddd;border-bottom:3px solid #ccc;display:flex;align-items:center;font-size:20px}
.qty .btn{width:20px;text-align:center;font-weight:600;color:#444;margin-left:3px}
.qty .n{margin-left:6px;padding-left:6px;border-left:1px solid #ddd;color:var(--red);font-size:18px;height:20px;line-height:20px}

.footer{position:absolute;left:0;top:940px;width:1300px;height:60px;background:var(--footer);border-top:5px solid #2f2f2f;color:#fff;font-size:13px}
.footer nav{position:absolute;left:150px;top:17px;display:flex;gap:10px}
.footer nav span.sep{color:#666}
.footer .copy{position:absolute;right:150px;top:17px}
</style>
</head>
<body>
<div class="page">
  <div class="pattern-band" role="img" aria-label="Light doodle pattern of food and kitchen items"></div>

  <div class="top-bar">
    <div class="rule" style="left:320px;width:42px"></div>
    <div class="call cond">Sună-ne la
      <span class="phone">
        <svg width="16" height="20" viewBox="0 0 16 20"><path d="M3 1l4 4-2 3c1 3 3 6 6 7l2-2 3 4-3 3C6 18 1 10 1 4z" fill="var(--yellow)"/></svg>0700 000 123</span>
    </div>
    <div class="dots"></div>
    <div class="auth cond" style="left:980px">
      <svg width="17" height="14" viewBox="0 0 17 14"><path d="M1 13V8c0-3 3-4 7-4V0l8 6-8 6V8c-4 0-6 1-7 5z" fill="#fff"/></svg>Login</div>
    <div class="auth cond" style="left:1062px">
      <svg width="18" height="14" viewBox="0 0 18 14"><circle cx="7" cy="4" r="3.5" fill="#fff"/><path d="M0 14c0-4 3-6 7-6s7 2 7 6z" fill="#fff"/><path d="M14 1v5M11.5 3.5h5" stroke="#fff" stroke-width="1.6"/></svg>Sign in</div>
    <div class="rule" style="left:1152px;width:148px"></div>
  </div>

  <svg class="brand-badge" viewBox="0 0 170 172" aria-hidden="true">
    <path d="M0 0h170v140l-22 30H22L0 140z" fill="var(--brown)"/>
    <path d="M6 0v137l19 27h120l19-27V0" fill="none" stroke="#4a3d3b" stroke-width="1.5"/>
  </svg>
  <div class="brand-circle">PlateGo</div>

  <aside class="cart cond">
    <div class="cart-head">
      <div class="cart-title">
        <svg width="17" height="14" viewBox="0 0 17 14"><path d="M0 1h3l2 8h9l2-6H4" fill="none" stroke="#fff" stroke-width="1.5"/><circle cx="6" cy="12" r="1.5" fill="#fff"/><circle cx="13" cy="12" r="1.5" fill="#fff"/></svg>Coșul meu</div>
      <div class="cart-detail">Detalii</div>
    </div>
    <div class="cart-item" style="margin-top:4px"><span>Zacuscă de vinete (3)</span><span class="pm">+-</span></div>
    <div class="cart-item"><span>Fasole bătută (3)</span><span class="pm">+-</span></div>
    <div class="cart-item"><span>"Taci și-nghite!" (1)</span><span class="pm">+-</span></div>
  </aside>

  <div class="menu-ghost cond">Meniu</div>

  <div class="resto-logo" role="img" aria-label="Restaurant photo"></div>
  <h1 class="resto-name cond" style="font-weight:400">La Hanul Vechi</h1>
  <div class="rating">
    <svg width="106" height="16" viewBox="0 0 106 16" aria-label="5 stele">
      <g fill="#e8b820">
        <path id="st" d="M8 1l2 5h5l-4 3 2 5-5-3-5 3 2-5-4-3h5z"/>
        <use href="#st" x="22"/><use href="#st" x="44"/><use href="#st" x="66"/><use href="#st" x="88"/>
      </g>
    </svg>
    <a>35 de review-uri</a>
  </div>

  <div class="meta cond" style="left:490px">
    <svg width="22" height="20" viewBox="0 0 22 20"><path d="M2 2l16 16M6 1l-5 5 4 4" stroke="var(--red)" stroke-width="2" fill="none"/></svg>Romanesc</div>
  <div class="meta cond" style="left:636px">
    <svg width="20" height="24" viewBox="0 0 20 24"><path d="M9 1h2v22H9z" fill="var(--red)"/><path d="M2 4h15l2 2-2 2H2zM3 11h15v4H3l-2-2z" fill="var(--red)"/></svg>3km</div>
  <div class="meta cond" style="left:724px">
    <svg width="20" height="16" viewBox="0 0 20 16"><g fill="var(--red)"><ellipse cx="8" cy="3" rx="7" ry="2.5"/><ellipse cx="8" cy="8" rx="7" ry="2.5"/><ellipse cx="8" cy="13" rx="7" ry="2.5"/><circle cx="16" cy="11" r="3.5"/></g></svg>&lt; 25ron</div>
  <div class="meta cond" style="left:847px">
    <svg width="20" height="20" viewBox="0 0 20 20"><circle cx="10" cy="10" r="8.5" fill="none" stroke="var(--red)" stroke-width="2"/><path d="M10 4v6l4 2" stroke="var(--red)" stroke-width="2" fill="none"/></svg>25min</div>

  <nav class="tabs cond">
    <span class="active">Gustări</span><span>Ciorbe</span><span>Pește</span><span>Pregătite în casă</span><span>Grătar</span><span>Garnituri</span><span>Salate</span><span>Desert</span><span>Băuturi</span>
  </nav>

  <section class="menu-grid">
    <div class="col">
      <div class="dish"><div><div class="dish-name">Zacuscă de vinete</div><div class="dish-price">11.00 RON</div></div><div class="qty"><span class="btn">+</span><span class="btn">-</span><span class="n">3</span></div></div>
      <div class="dish"><div><div class="dish-name">Salată de icre de crap</div><div class="dish-price">16.00 RON</div></div><div class="qty"><span class="btn">+</span><span class="btn">-</span><span class="n">0</span></div></div>
      <div class="dish"><div><div class="dish-name">Salata de icre de știucă</div><div class="dish-price">22.00 RON</div></div><div class="qty"><span class="btn">+</span><span class="btn">-</span><span class="n">0</span></div></div>
      <div class="dish"><div><div class="dish-name">Fasole bătută</div><div class="dish-price">11.00 RON</div></div><div class="qty"><span class="btn">+</span><span class="btn">-</span><span class="n">3</span></div></div>
      <div class="dish"><div><div class="dish-name">Salată Isaccea</div><div class="dish-price">19.00 RON</div></div><div class="qty"><span class="btn">+</span><span class="btn">-</span><span class="n">0</span></div></div>
      <div class="dish"><div><div class="dish-name">Colțunași cu mânătărci</div><div class="dish-price">23.00 RON</div></div><div class="qty"><span class="btn">+</span><span class="btn">-</span><span class="n">0</span></div></div>
    </div>
    <div class="col">
      <div class="dish"><div><div class="dish-name">Chiperchi</div><div class="dish-price">16.00 RON</div></div><div class="qty"><span class="btn">+</span><span class="btn">-</span><span class="n">0</span></div></div>
      <div class="dish"><div><div class="dish-name">Salată ciobănească</div><div class="dish-price">13.00 RON</div></div><div class="qty"><span class="btn">+</span><span class="btn">-</span><span class="n">0</span></div></div>
      <div class="dish"><div><div class="dish-name">“Taci și-nghite”</div><div class="dish-price">10.00 RON</div></div><div class="qty"><span class="btn">+</span><span class="btn">-</span><span class="n">1</span></div></div>
      <div class="dish"><div><div class="dish-name">Salată de cartofi</div><div class="dish-price">10.00 RON</div></div><div class="qty"><span class="btn">+</span><span class="btn">-</span><span class="n">0</span></div></div>
      <div class="dish"><div><div class="dish-name">Tarator</div><div class="dish-price">8.00 RON</div></div><div class="qty"><span class="btn">+</span><span class="btn">-</span><span class="n">0</span></div></div>
      <div class="dish"><div><div class="dish-name">Salată de vinete</div><div class="dish-price">13.00 RON</div></div><div class="qty"><span class="btn">+</span><span class="btn">-</span><span class="n">0</span></div></div>
    </div>
    <div class="col">
      <div class="dish"><div><div class="dish-name">Jumări Românești</div><div class="dish-price">7.00 RON <em>(100gr/por)</em></div></div><div class="qty"><span class="btn">+</span><span class="btn">-</span><span class="n">0</span></div></div>
      <div class="dish"><div><div class="dish-name">Tobă Țărănească</div><div class="dish-price">7.00 RON <em>(100gr/por)</em></div></div><div class="qty"><span class="btn">+</span><span class="btn">-</span><span class="n">0</span></div></div>
      <div class="dish"><div><div class="dish-name">Slănină Afumată</div><div class="dish-price">3.00 RON <em>(50gr/por)</em></div></div><div class="qty"><span class="btn">+</span><span class="btn">-</span><span class="n">0</span></div></div>
      <div class="dish"><div><div class="dish-name">Șorici</div><div class="dish-price">9.00 RON <em>(50gr/por)</em></div></div><div class="qty"><span class="btn">+</span><span class="btn">-</span><span class="n">0</span></div></div>
      <div class="dish"><div><div class="dish-name">Caltaboș</div><div class="dish-price">7.00 RON <em>(100gr/por)</em></div></div><div class="qty"><span class="btn">+</span><span class="btn">-</span><span class="n">0</span></div></div>
      <div class="dish"><div><div class="dish-name">Lebăr</div><div class="dish-price">6.00 RON <em>(100gr/por)</em></div></div><div class="qty"><span class="btn">+</span><span class="btn">-</span><span class="n">0</span></div></div>
    </div>
  </section>

  <footer class="footer">
    <nav><span>Contactează-ne</span><span class="sep">|</span><span>Despre noi</span><span class="sep">|</span><span>Partenerii noștri</span><span class="sep">|</span><span>FAQ</span><span class="sep">|</span><span>Devino partener</span></nav>
    <div class="copy">Copyright © 2013 platego.ro. Toate drepturile rezervate.</div>
  </footer>
</div>
</body>
</html>
```